SHIELD BEFORE SUIT

I'm virtually ready to launch my site, but I have a number of edits and modifications that need to be implemented. More importantly, I'm always looking to improve my site, particularly now that I am making my proverbial "FIRST IMPRESSION." Thus, I'm willing to see if there is someone who can add creativity and perhaps improve what I already have, particularly on the All Important Front Page.

```html
<!DOCTYPE html>
<html lang="en">
<head>
<meta charset="utf-8">
<title>Shield Before Suit</title>
<link href="https://fonts.googleapis.com/css2?family=Archivo:wght@400;600;700&family=Noto+Serif:wght@400;600;700&family=PT+Serif:wght@400;700&display=swap" rel="stylesheet">
<style>
:root{
  --navy:#0f2452;
  --navy-deep:#0b1f4a;
  --red:#a4000f;
  --red-bright:#b8000f;
  --ink:#1b1b1b;
  --white:#ffffff;
  --black:#000000;
}
*{margin:0;padding:0;box-sizing:border-box}
html,body{width:1200px;height:3523px;overflow:hidden;background:var(--white)}
body{position:relative;font-family:"PT Serif",serif;color:var(--ink)}
.abs{position:absolute}
.sans{font-family:"Archivo",sans-serif}

/* header */
.brand{left:118px;top:56px;display:flex;align-items:center;gap:10px;font-family:"Noto Serif",serif;font-weight:700;font-size:17px;color:var(--navy);white-space:nowrap}
.brand .dot{width:24px;height:24px;border-radius:50%;background:var(--red);flex:none}
.topinfo{top:36px;font-family:"Archivo",sans-serif;font-size:12.5px;font-weight:600;letter-spacing:.4px;display:flex;align-items:center;gap:10px;color:var(--ink);white-space:nowrap}
.navbar{left:268px;top:84px;width:932px;height:56px}
.nav{top:84px;height:56px;display:flex;align-items:center;font-family:"Archivo",sans-serif;font-weight:700;font-size:15px;letter-spacing:1px;color:var(--white)}

/* hero */
.hero-photo{left:0;top:140px;width:1200px;height:546px;background:linear-gradient(120deg,#c58c55 0%,#e4c4a0 25%,#8d8b8a 45%,#4a5c78 100%)}
.hero-title{left:617px;top:222px;font-size:40px;font-weight:700;color:var(--white);letter-spacing:1px;font-family:"Noto Serif",serif;white-space:nowrap}
.hero-text{left:620px;top:306px;width:500px;font-family:"Noto Serif",serif;font-size:15.5px;line-height:31px;color:var(--white);letter-spacing:.4px}
.btn{top:544px;height:54px;background:var(--red-bright);color:var(--white);border-radius:5px;display:flex;align-items:center;justify-content:center;font-family:"Noto Serif",serif;font-weight:700;font-size:15.5px;letter-spacing:1px}

/* section titles */
.sec-title{font-family:"Noto Serif",serif;font-size:40px;font-weight:400;width:1200px;text-align:center;left:0}
.stars{width:54px;height:24px}

/* about */
.about-lead{left:137px;top:876px;width:900px;font-size:15.5px;line-height:34px}
.about-story{left:609px;top:1004px;width:490px;font-size:15.5px;line-height:34px}
.frame{border:3px solid}

/* services */
.svc-band{left:0;top:1451px;width:732px;height:701px;background:var(--navy-deep)}
.svc-photo{left:732px;top:1451px;width:468px;height:701px;background:linear-gradient(160deg,#e7edf2 0%,#b8c6d6 40%,#3c4a66 75%,#1d2a44 100%)}
.svc-title{left:139px;top:1500px;font-family:"Noto Serif",serif;font-size:38px;color:var(--white)}
.svc{width:250px;text-align:center;color:var(--white)}
.svc h3{font-family:"Noto Serif",serif;font-weight:400;font-size:20px;line-height:31px;margin-top:10px}
.svc p{font-family:"PT Serif",serif;font-weight:700;font-size:13px;line-height:26px;margin-top:4px}
.svc svg{display:block;margin:0 auto}

/* faq */
.faq{left:248px;width:697px;height:68px;border:1px solid #9c9c9c;box-shadow:0 2px 4px rgba(0,0,0,.25);background:var(--white)}
.faq .q{position:absolute;left:16px;top:0;height:66px;display:flex;align-items:center;font-size:15.5px}
.faq .tog{position:absolute;right:-1px;top:-1px;width:66px;height:68px;background:var(--red);display:flex;align-items:center;justify-content:center}
.faq-body{left:248px;top:2518px;width:697px;height:95px;border:1px solid #6b6b6b;padding:10px 16px;font-size:12.5px;line-height:33px}

/* cta + footer */
.footer{left:0;top:3000px;width:1200px;height:523px;background:var(--black)}
.cta{left:144px;top:2888px;width:896px;height:192px;background:var(--red)}
.cta h2{position:absolute;left:0;top:38px;width:896px;text-align:center;font-family:"Noto Serif",serif;font-weight:600;font-size:37px;color:var(--white)}
.cta a{position:absolute;left:322px;top:115px;width:269px;height:43px;background:var(--white);border-radius:4px;display:flex;align-items:center;justify-content:center;font-family:"Noto Serif",serif;font-weight:600;font-size:19px;color:var(--black);text-decoration:none;letter-spacing:.5px}
.foot-text{left:133px;top:3222px;width:400px;font-size:15px;line-height:33px;color:var(--white)}
.foot-head{top:3190px;font-size:15px;font-weight:700;color:var(--white)}
.foot-link{font-size:15px;color:var(--white)}
.foot-contact{left:862px;color:var(--white);display:flex;align-items:flex-start;gap:10px}
.rule{left:0;top:3465px;width:1200px;height:1px;background:#444}
.copy{left:0;top:3489px;width:1200px;text-align:center;font-size:12px;color:var(--white);letter-spacing:.3px}
</style>
</head>
<body>

<!-- header -->
<div class="abs brand"><span class="dot"></span><span>Shield Before Suit</span></div>

<div class="abs topinfo" style="left:306px">
  <svg width="20" height="22" viewBox="0 0 20 22" fill="none" stroke="#222" stroke-width="1.4"><path d="M10 21s7-7 7-12a7 7 0 0 0-14 0c0 5 7 12 7 12z"/><circle cx="10" cy="9" r="2.6"/></svg>
  <span>4820 Canyon Ridge Rd., Suite 210 Mesa, Arizona 85201</span>
</div>
<div class="abs topinfo" style="left:758px">
  <svg width="22" height="22" viewBox="0 0 24 24" fill="none" stroke="#222" stroke-width="1.4"><path d="M5 3h4l2 5-3 2a12 12 0 0 0 6 6l2-3 5 2v4a2 2 0 0 1-2 2A18 18 0 0 1 3 5a2 2 0 0 1 2-2z"/></svg>
  <span>480.555.0192</span>
</div>
<div class="abs topinfo" style="left:915px">
  <svg width="20" height="16" viewBox="0 0 20 16" fill="none" stroke="#222" stroke-width="1.4"><rect x="1" y="1" width="18" height="14"/><path d="M1 1l9 8 9-8"/></svg>
  <span>WWW.SHIELDBEFORESUIT.COM</span>
</div>

<svg class="abs navbar" viewBox="0 0 932 56" preserveAspectRatio="none"><polygon points="32,0 932,0 932,56 0,56" fill="var(--red)"/></svg>
<div class="abs nav" style="left:433px">HOME</div>
<div class="abs nav" style="left:574px">ABOUT US</div>
<div class="abs nav" style="left:751px">PRODUCT</div>
<div class="abs nav" style="left:922px">CONTACT US</div>

<!-- hero -->
<div class="abs hero-photo" role="img" aria-label="Smiling businessman in a blue suit standing in a bright office meeting room with colleagues at a table"></div>
<svg class="abs" style="left:0;top:140px" width="1200" height="546" viewBox="0 0 1200 546"><polygon points="610,0 1200,0 1200,546 405,546" fill="var(--navy)" opacity=".96"/></svg>
<div class="abs hero-title">SHIELD BEFORE SUIT</div>
<div class="abs hero-text">BUSINESS OWNERS: Shield Before Suit (SBS) Is An Extremely Affordable Legal Service Plan (As Little As $8.00 Per Month) That INSULATES Business Owners From Unwarranted LEGAL CLAIMS And Expensive LAWSUITS. Our Plan Uses Local, Experienced, Quality Attorneys Who Focus On PROBLEM PREVENTION Using Proprietary Tools Available Only To SBS Members.</div>
<div class="abs btn" style="left:618px;width:162px">LEARN MORE</div>
<div class="abs btn" style="left:798px;width:295px">SCHEDULE FREE CONSULTATION</div>

<!-- about -->
<div class="abs sec-title" style="top:760px">About Us</div>
<svg class="abs stars" style="left:573px;top:828px" viewBox="0 0 54 24"><polygon points="9,1 11.5,7 18,7 13,11 15,18 9,14 3,18 5,11 0,7 6.5,7" fill="var(--red)"/><polygon points="27,6 29.5,12 36,12 31,16 33,23 27,19 21,23 23,16 18,12 24.5,12" fill="var(--red)"/><polygon points="45,1 47.5,7 54,7 49,11 51,18 45,14 39,18 41,11 36,7 42.5,7" fill="var(--navy)"/></svg>
<div class="abs about-lead">SBS is a group of attorney and legal assistants with many years of experience in litigation, who are devoted to PREVENTING<br>LEGAL CLAIMS and COSTLY LAWSUITS through a variety of FREE and VERY AFFORDABLE services described below.<br>OUR UNIQUE SERVICE PLAN MAKES IT POSSIBLE FOR US TO PREVENT THE LAWSUITS.</div>

<div class="abs frame" style="left:115px;top:1073px;width:409px;height:290px;border-color:var(--navy)"></div>
<div class="abs frame" style="left:158px;top:1038px;width:410px;height:291px;border-color:var(--red)"></div>
<div class="abs" style="left:185px;top:1010px;width:392px;height:300px;background:linear-gradient(110deg,#8a8a84 0%,#c9c6b8 40%,#a9b48e 70%,#d7c07a 100%)" role="img" aria-label="Close-up of a hundred dollar bill with the portrait wearing a face mask"></div>
<div class="abs about-story">A homebuilding company was sued by a former employee who claimed to have been promised a more favorable sales area, which claim was disputed by the homebuilder. There was no evidence that such a promise had been made, other than the plaintiff's oral testimony. The company had the case dismissed, but spent $10,000 defending the case.<br>And even though it was awarded its attorney's fees, the plaintiff proved uncollectible. Had the company been an SBS member, the case likely would never have been filed. Call for your FREE CONSULTATION and let us show you why the plaintiff likely would not have found a contingency attorney</div>

<!-- services -->
<div class="abs svc-band"></div>
<div class="abs svc-photo" role="img" aria-label="Senior businesswoman and young businessman in suits reviewing a folder together"></div>
<div class="abs svc-title">Our Services</div>
<svg class="abs stars" style="left:143px;top:1574px" viewBox="0 0 54 24"><polygon points="9,1 11.5,7 18,7 13,11 15,18 9,14 3,18 5,11 0,7 6.5,7" fill="#fff"/><polygon points="27,6 29.5,12 36,12 31,16 33,23 27,19 21,23 23,16 18,12 24.5,12" fill="#fff"/><polygon points="45,1 47.5,7 54,7 49,11 51,18 45,14 39,18 41,11 36,7 42.5,7" fill="#fff"/></svg>

<div class="abs svc" style="left:108px;top:1622px">
  <svg width="72" height="60" viewBox="0 0 72 60" fill="none" stroke="#fff" stroke-width="2"><circle cx="14" cy="8" r="5"/><circle cx="58" cy="8" r="5"/><path d="M8 18h12v22M64 18H52v22M4 18v40M68 18v40M20 34h32M36 34v24M8 40h12v18M64 40H52v18"/></svg>
  <h3>Free Initial<br>Consultation</h3>
  <p>As a prospective Shield Before Suit ("SBS") member, we urge you to schedule an initial consultation</p>
</div>
<div class="abs svc" style="left:418px;top:1620px">
  <svg width="60" height="62" viewBox="0 0 60 62" fill="none" stroke="#fff" stroke-width="2"><path d="M8 2h30l12 12v30M8 2v50h20"/><path d="M16 16h18M16 24h24M16 32h14"/><path d="M30 50l8-8 8 4 10-6M34 56l6-4"/></svg>
  <h3>Proprietary<br>Contract Language</h3>
  <p>SBS members are entitled to incorporate exclusive proprietary contract</p>
</div>
<div class="abs svc" style="left:91px;top:1865px">
  <svg width="76" height="78" viewBox="0 0 76 78" fill="none" stroke="#fff" stroke-width="2"><rect x="4" y="2" width="20" height="14" rx="2"/><rect x="48" y="2" width="20" height="14" rx="2"/><circle cx="20" cy="34" r="8"/><circle cx="56" cy="34" r="8"/><path d="M6 76V56a14 12 0 0 1 28 0v20M42 76V56a14 12 0 0 1 28 0v20"/></svg>
  <h3>Free<br>Consultation</h3>
  <p>SBS members can call their local SBS Attorney any time</p>
</div>
<div class="abs svc" style="left:418px;top:1870px">
  <svg width="66" height="66" viewBox="0 0 66 66" fill="none" stroke="#fff" stroke-width="2"><circle cx="30" cy="16" r="10"/><path d="M8 64V46a22 14 0 0 1 44 0v18"/><path d="M48 40h14M55 36v24M48 48l-3 8h6zM62 48l-3 8h6z"/></svg>
  <h3>Free Attorney<br>Letters</h3>
  <p>In addition to free monthly consultations</p>
</div>
<svg class="abs" style="left:422px;top:2104px" width="38" height="12"><circle cx="6" cy="6" r="4.5" fill="#fff"/><circle cx="19" cy="6" r="4.5" fill="#7ea6e0"/><circle cx="32" cy="6" r="4.5" fill="#fff"/></svg>

<!-- faq -->
<div class="abs sec-title" style="top:2234px">Frequently Asked Questions</div>
<svg class="abs stars" style="left:573px;top:2302px" viewBox="0 0 54 24"><polygon points="9,1 11.5,7 18,7 13,11 15,18 9,14 3,18 5,11 0,7 6.5,7" fill="var(--red)"/><polygon points="27,6 29.5,12 36,12 31,16 33,23 27,19 21,23 23,16 18,12 24.5,12" fill="var(--red)"/><polygon points="45,1 47.5,7 54,7 49,11 51,18 45,14 39,18 41,11 36,7 42.5,7" fill="var(--navy)"/></svg>

<div class="abs faq" style="top:2364px"><div class="q">Why should I be concerned about legal claims?</div><div class="tog"><svg width="14" height="8" viewBox="0 0 14 8" fill="none" stroke="#fff" stroke-width="1.6"><path d="M1 1l6 6 6-6"/></svg></div></div>
<div class="abs faq" style="top:2450px"><div class="q" style="color:var(--navy)">Provide more details about the value of SBS's contract language.</div><div class="tog"><svg width="14" height="8" viewBox="0 0 14 8" fill="none" stroke="#fff" stroke-width="1.6"><path d="M1 1l6 6 6-6"/></svg></div></div>
<div class="abs faq-body">Lorem ipsum dolor sit amet, consectetur adipiscing elit. Suspendisse varius enim in eros elementum tristique. Duis cursus, mi quis viverra ornare, eros dolor interdum nulla, ut commodo diam libero vitae erat.</div>
<div class="abs faq" style="top:2634px"><div class="q">What does an SBS membership cost?</div><div class="tog"><svg width="14" height="8" viewBox="0 0 14 8" fill="none" stroke="#fff" stroke-width="1.6"><path d="M1 1l6 6 6-6"/></svg></div></div>
<div class="abs faq" style="top:2720px"><div class="q">Do you have a Referral Program?</div><div class="tog"><svg width="14" height="8" viewBox="0 0 14 8" fill="none" stroke="#fff" stroke-width="1.6"><path d="M1 1l6 6 6-6"/></svg></div></div>

<!-- cta + footer -->
<div class="abs footer"></div>
<div class="abs cta"><h2>Contact Us For A Free Consultation</h2><a>FREE CONSULTATION</a></div>

<div class="abs brand" style="left:150px;top:3136px;color:var(--white)"><span class="dot"></span><span>Shield Before Suit</span></div>
<div class="abs foot-text">Contact Us For A Free Consultation And Receive A FREE OVERVIEW Of Your Business To See If You Are Truly Insulated From Legal Claims.<br>Contact us to find out how you can join us to PREVENT THE LAWSUITS!!</div>
<svg class="abs" style="left:131px;top:3406px" width="260" height="24"><circle cx="8" cy="12" r="6" fill="#fff"/><circle cx="48" cy="12" r="6" fill="none" stroke="#fff" stroke-width="1.5"/><circle cx="89" cy="12" r="6" fill="none" stroke="#fff" stroke-width="1.5"/><rect x="113" y="1" width="136" height="22" rx="2" fill="#fff"/></svg>

<div class="abs foot-head" style="left:593px">QUICK LINKS</div>
<div class="abs foot-link" style="left:593px;top:3226px">Home</div>
<div class="abs foot-link" style="left:593px;top:3259px">About</div>
<div class="abs foot-link" style="left:593px;top:3292px">Services</div>
<div class="abs foot-link" style="left:593px;top:3325px">FAQ's</div>
<div class="abs foot-link" style="left:704px;top:3226px">Contact Us</div>
<div class="abs foot-link" style="left:704px;top:3259px">Terms of Services</div>
<div class="abs foot-link" style="left:704px;top:3292px">Privacy policy</div>

<div class="abs foot-head" style="left:862px">CONTACT US</div>
<div class="abs foot-contact sans" style="top:3234px;font-size:16px;font-weight:600"><svg width="22" height="22" viewBox="0 0 24 24" fill="none" stroke="#fff" stroke-width="1.4"><path d="M5 3h4l2 5-3 2a12 12 0 0 0 6 6l2-3 5 2v4a2 2 0 0 1-2 2A18 18 0 0 1 3 5a2 2 0 0 1 2-2z"/></svg><span>480.555.0192</span></div>
<div class="abs foot-contact" style="top:3282px;font-size:12.5px"><svg width="20" height="16" viewBox="0 0 20 16" fill="none" stroke="#fff" stroke-width="1.4"><rect x="1" y="1" width="18" height="14"/><path d="M1 1l9 8 9-8"/></svg><span>WWW.SHIELDBEFORESUIT.COM</span></div>
<div class="abs foot-contact" style="top:3326px;font-size:16px;line-height:31px;font-family:'Noto Serif',serif"><svg width="20" height="24" viewBox="0 0 20 22" fill="none" stroke="#fff" stroke-width="1.4"><path d="M10 21s7-7 7-12a7 7 0 0 0-14 0c0 5 7 12 7 12z"/><circle cx="10" cy="9" r="2.6"/></svg><span>4820 Canyon Ridge Rd.,<br>Suite 210 Mesa,<br>Arizona 85201</span></div>

<div class="abs rule"></div>
<div class="abs copy">Copyright© 2023 SHIELDBEFORESUIT.NET | All Rights Reserved</div>

</body>
</html>
```